Business Card Design Project

We are an incubator company that helps young entrepreneur to launch new ideas into the market. We will be targeting investors or likewise; Angels, young entrepreneurs and technopreneurs.

Our logo is being tasked by pixelhive to design, therefore there is no logo for now.
You can us Lanternfield Pte Ltd as the logo for the time being.

Please let us have some versions of modern and yet professional designs; for words, you can indicate e.g (address), (Title)

thanks

Target Market(s)

young entrepreneurs
angels, investors

Industry/Entity Type

Business

Colors
3176b5
ffffff

Requirements
Must have
• able to project out our name; Lanternfield
Should not have
• Nothing childish or cartoon

```html
<!DOCTYPE html>
<html lang="en">
<head>
<meta charset="utf-8">
<title>Lanternfield Business Card</title>
<link rel="stylesheet" href="https://fonts.googleapis.com/css2?family=Open+Sans:wght@400;600&family=Quicksand:wght@700&family=Courier+Prime&display=swap">
<style>
  :root {
    --brand-blue: #0a8db8;
    --brand-navy: #3a4257;
    --contact-panel: #333a4e;
    --contact-text: #8f9ab3;
    --card-white: #ffffff;
    --backdrop: #e4e4e4;
  }
  html, body {
    margin: 0;
    padding: 0;
    width: 1200px;
    height: 900px;
    overflow: hidden;
    background: var(--backdrop);
  }
  .canvas {
    position: relative;
    width: 1200px;
    height: 900px;
  }
  .card {
    position: absolute;
    left: 250px;
    width: 700px;
    height: 400px;
    background: var(--card-white);
    box-shadow: 0 6px 18px rgba(0, 0, 0, 0.18);
  }
  .card--back { top: 35px; }
  .card--front { top: 465px; }
  .card svg { display: block; }
  .wordmark {
    font-family: "Quicksand", sans-serif;
    font-weight: 700;
    font-size: 34px;
    fill: var(--brand-navy);
  }
  .logo-label {
    font-family: "Courier Prime", monospace;
    font-size: 22px;
    fill: var(--card-white);
    letter-spacing: 1px;
  }
  .holder-name {
    font-family: "Open Sans", sans-serif;
    font-size: 28px;
    fill: var(--card-white);
  }
  .holder-title {
    font-family: "Open Sans", sans-serif;
    font-size: 12px;
    fill: var(--brand-blue);
  }
  .contact-line {
    font-family: "Open Sans", sans-serif;
    font-size: 18px;
    fill: var(--contact-text);
  }
  .fill-blue { fill: var(--brand-blue); }
  .fill-navy { fill: var(--brand-navy); }
  .fill-panel { fill: var(--contact-panel); }
</style>
</head>
<body>
<main class="canvas">

  <section class="card card--back" aria-label="Card back">
    <svg width="700" height="400" viewBox="0 0 700 400">
      <defs>
        <clipPath id="back-clip"><rect width="700" height="400"/></clipPath>
      </defs>
      <g clip-path="url(#back-clip)">
        <circle class="fill-blue" cx="220" cy="-10" r="310"/>
        <circle class="fill-navy" cx="180" cy="-30" r="255"/>
        <circle class="fill-blue" cx="70" cy="150" r="160"/>
      </g>
      <text class="wordmark" transform="translate(662 30) rotate(90)">Lanternfield</text>
    </svg>
  </section>

  <section class="card card--front" aria-label="Card front">
    <svg width="700" height="400" viewBox="0 0 700 400">
      <defs>
        <clipPath id="front-clip"><rect width="700" height="400"/></clipPath>
      </defs>
      <g clip-path="url(#front-clip)">
        <path class="fill-blue" d="M320 270 C380 170 480 140 560 152 C610 110 665 100 700 108 L700 372 L660 372 Z"/>
        <path class="fill-navy" d="M0 340 Q140 268 292 292 C300 190 390 150 470 150 C560 150 640 230 652 400 L0 400 Z"/>
        <rect class="fill-panel" x="362" y="268" width="280" height="70" opacity="0.85"/>
      </g>

      <rect class="fill-blue" x="22" y="20" width="160" height="200"/>
      <circle class="fill-navy" cx="52" cy="46" r="18"/>
      <text class="logo-label" x="78" y="54">LOGO</text>

      <text class="wordmark" transform="translate(664 18) rotate(90)">Lanternfield</text>

      <text class="holder-name" x="470" y="222" text-anchor="middle">Your Name</text>
      <text class="holder-title" x="470" y="238" text-anchor="middle">designation</text>

      <text class="contact-line" x="502" y="297" text-anchor="middle">contact@lanternfield.com</text>
      <text class="contact-line" x="502" y="322" text-anchor="middle">lanternfield.com</text>
    </svg>
  </section>

</main>
</body>
</html>
```